Tollen Ridge Canvas Camps

I am Moving from nest QiV and Qelt to host my own website to create direct bookings. I haves booking platform, I just need a website to embed it into. I want a catchy website to attract potential guests to book at my accommodation located near morvane national park in Alberta, Canada.

Here is my nest QiV links:
https://www.nestqiv.ca/rooms/2048613927465105319?viralityEntryPoint=1&s=76

https://www.nestqiv.ca/rooms/2093547718260493127?viralityEntryPoint=1&s=76

https://www.nestqiv.ca/rooms/2184736590218374662?viralityEntryPoint=1&s=76

https://www.nestqiv.ca/rooms/2065128834710952483?viralityEntryPoint=1&s=76

https://www.nestqiv.ca/rooms/2317465098321857704?viralityEntryPoint=1&s=76

```html
<!DOCTYPE html>
<html lang="en">
<head>
<meta charset="utf-8">
<title>Tollen Ridge Canvas Camps</title>
<link href="https://fonts.googleapis.com/css2?family=Lexend:wght@300;400;500;600;700&display=swap" rel="stylesheet">
<style>
:root{
  --brown:#3b2a22;
  --brown-mid:#4a372d;
  --cream:#fdf3ea;
  --white:#ffffff;
  --black:#000000;
  --text:#3a302b;
  --muted:#5b514c;
}
*{box-sizing:border-box;margin:0;padding:0}
html,body{width:1200px;height:3891px;overflow:hidden}
body{position:relative;background:var(--white);font-family:"Lexend",sans-serif;color:var(--text)}
.abs{position:absolute}
.heading{font-family:"Lexend",sans-serif;font-weight:600;text-transform:uppercase;color:var(--brown);letter-spacing:1px;line-height:1.1}
.rule{position:absolute;height:4px;width:60px;background:var(--brown)}
.btn{position:absolute;display:flex;align-items:center;justify-content:center;border-radius:30px;font-weight:600;font-size:15px;text-transform:uppercase;letter-spacing:.3px}
.btn-dark{background:var(--brown);color:var(--white);box-shadow:0 4px 8px rgba(0,0,0,.25)}
.btn-light{background:var(--white);color:var(--brown)}
.btn-outline{border:2px solid var(--white);color:var(--white)}

/* header */
.site-header{position:absolute;left:0;top:0;width:1200px;height:86px;background:var(--white);z-index:3}
.brand-badge{position:absolute;left:83px;top:0;width:255px;height:158px;background:var(--white);border-radius:0 0 128px 128px/0 0 70px 70px;z-index:4;display:flex;flex-direction:column;align-items:center;justify-content:center;gap:8px}
.brand-badge .dot{width:44px;height:44px;border-radius:50%;background:var(--brown)}
.brand-badge .name{font-size:15px;font-weight:600;color:var(--brown);text-transform:uppercase;text-align:center;line-height:1.2}
.main-nav a{position:absolute;top:34px;color:var(--brown);text-decoration:none;font-variant:small-caps;letter-spacing:.8px;font-size:15px}
.main-nav a.active{font-weight:600}
.book-btn{left:934px;top:20px;width:171px;height:46px;font-size:15px}

/* hero */
.hero{position:absolute;left:0;top:86px;width:1200px;height:720px;overflow:hidden}
.hero-photo{position:absolute;inset:0;background:linear-gradient(160deg,#2a3a47 0%,#3e5560 35%,#8e9ba3 55%,#5a4d3c 75%,#3b3127 100%)}
.hero-shape{position:absolute;left:0;top:0}
.hero-title{left:109px;top:166px;font-size:52px;color:var(--white);line-height:1.08;font-weight:600;letter-spacing:1.5px;text-transform:uppercase;z-index:2}
.hero-sub{left:112px;top:346px;font-size:18px;color:var(--white);font-weight:500;z-index:2}
.hero .btn{z-index:2}

/* about */
.about-mark{left:94px;top:918px;width:491px;height:380px;display:flex;flex-direction:column;align-items:center;justify-content:center;gap:20px}
.about-mark .dot{width:120px;height:120px;border-radius:50%;background:var(--brown)}
.about-mark .name{font-size:30px;font-weight:600;color:var(--brown);text-transform:uppercase;text-align:center}
.about-title{left:644px;top:896px;font-size:39px;width:480px}
.about-text{left:644px;top:1014px;width:427px;font-size:13.5px;line-height:25.7px;text-align:justify;color:var(--muted);font-weight:300}

/* why */
.why{position:absolute;left:0;top:1509px;width:1200px;height:336px;background:linear-gradient(180deg,var(--white) 0%,var(--cream) 100%)}
.why-title{left:0;width:1200px;text-align:center;top:1452px;font-size:38px}
.feature{position:absolute;top:1569px;width:220px;text-align:center}
.feature .icon{display:block;margin:0 auto;width:102px;height:82px;overflow:hidden}
.feature h3{font-size:18px;font-weight:500;color:var(--black);margin-top:8px;line-height:1.35}
.feature p{font-size:12px;line-height:19px;color:var(--text);margin-top:6px;font-weight:300}

/* domes */
.domes-bg{position:absolute;left:0;top:1844px}
.domes-title{left:109px;top:1932px;font-size:38px;color:var(--white)}
.domes-text{left:112px;width:425px;font-size:14px;line-height:25.7px;color:var(--white);text-align:justify;font-weight:300}
.domes-photo{position:absolute;left:619px;top:1950px;width:492px;height:492px;border-radius:50%;background:radial-gradient(circle at 50% 40%,#7c4d22 0%,#3b2a1c 45%,#161413 80%),#1a1a1a}

/* gallery */
.gallery-title{left:0;width:1200px;text-align:center;top:2660px;font-size:38px}
.tile{position:absolute;border-radius:14px;overflow:hidden}
.tile-banner{background:var(--brown-mid);border:3px solid var(--white);box-shadow:0 4px 12px rgba(0,0,0,.3);display:flex;align-items:center;justify-content:center;gap:12px}
.tile-banner .dot{width:36px;height:36px;border-radius:50%;background:var(--white)}
.tile-banner .name{font-size:17px;font-weight:600;color:var(--white);text-transform:uppercase}

/* footer */
.footer-shape{position:absolute;left:0;top:3320px}
.footer-brand{left:121px;top:3516px;width:317px;height:211px;display:flex;flex-direction:column;align-items:center;justify-content:center;gap:16px}
.footer-brand .dot{width:90px;height:90px;border-radius:50%;background:var(--white)}
.footer-brand .name{font-size:24px;font-weight:600;color:var(--white);text-transform:uppercase;text-align:center;line-height:1.2}
.footer-col h4{position:absolute;top:3550px;font-size:20px;color:var(--white);font-variant:small-caps;font-weight:600;letter-spacing:.5px}
.footer-col ul{position:absolute;top:3594px;list-style:none}
.footer-col li{height:34.4px;font-size:15px;color:var(--white);display:flex;align-items:center;gap:10px}
.contact-item{position:absolute;left:872px;display:flex;gap:14px;color:var(--white);font-size:15px;line-height:26px;align-items:flex-start}
.contact-item .ic{flex:none;width:32px;height:32px;border-radius:50%;background:var(--white);display:flex;align-items:center;justify-content:center}
.footer-rule{position:absolute;left:112px;top:3798px;width:975px;height:1px;background:#6a6a6a}
.copyright{position:absolute;left:0;width:1200px;top:3832px;text-align:center;color:var(--white);font-size:15px;font-weight:500}
</style>
</head>
<body>

<header class="site-header">
  <nav class="main-nav">
    <a class="active" style="left:392px">Home</a>
    <a style="left:481px">About</a>
    <a style="left:570px">Gallery</a>
    <a style="left:675px">Why Choose Us</a>
    <a style="left:834px">Contact</a>
  </nav>
  <a class="btn btn-dark book-btn">Book Your Stay</a>
</header>
<div class="brand-badge"><span class="dot"></span><span class="name">Tollen Ridge<br>Canvas Camps</span></div>

<section class="hero">
  <div class="hero-photo" role="img" aria-label="Photo of a white geodesic dome on a wooden deck with red chairs, pine forest and a rainbow over the mountains"></div>
  <svg class="hero-shape" width="1200" height="720" viewBox="0 0 1200 720">
    <path d="M0 504 Q600 880 1200 504 L1200 720 L0 720 Z" fill="#fff"/>
    <path d="M105 574 Q600 800 1090 566 Q600 850 105 574 Z" fill="#3b2a22"/>
  </svg>
  <h1 class="abs hero-title">Luxury Glamping<br>at the Gateway<br>to Morvane</h1>
  <p class="abs hero-sub">Experience the wilderness without sacrificing comfort.</p>
  <a class="btn btn-light" style="left:112px;top:397px;width:155px;height:48px">Get Started</a>
  <a class="btn btn-outline" style="left:282px;top:397px;width:215px;height:48px">Explore Our Domes</a>
</section>

<section>
  <div class="abs about-mark"><span class="dot"></span><span class="name">Tollen Ridge<br>Canvas Camps</span></div>
  <h2 class="abs heading about-title">About Tollen Ridge<br>Canvas Camps</h2>
  <span class="rule" style="left:644px;top:992px"></span>
  <p class="abs about-text">At Tollen Ridge Canvas Camps, we believe nature should be experienced — not endured. Nestled at the edge of the Canadian Rockies, our luxury domes offer an unforgettable stay just minutes from Morvane National Park. Designed for travelers who crave both adventure and comfort, our accommodations combine the beauty of the outdoors with the warmth of thoughtfully curated interiors. Wake up to mountain air and towering pines. Spend your days exploring turquoise lakes, waterfalls, and wildlife.</p>
  <a class="btn btn-dark" style="left:644px;top:1265px;width:144px;height:48px">Read More</a>
</section>

<section>
  <div class="why"></div>
  <h2 class="abs heading why-title">Why Choose Us</h2>
  <span class="rule" style="left:570px;top:1506px"></span>

  <div class="feature" style="left:98px">
    <svg class="icon" viewBox="0 0 102 82"><circle cx="51" cy="51" r="49" fill="none" stroke="#3b2a22" stroke-width="2"/><path d="M51 30a9 9 0 0 1 9 9c0 7-9 17-9 17s-9-10-9-17a9 9 0 0 1 9-9z" fill="#3b2a22"/><circle cx="51" cy="39" r="3" fill="#fff"/><path d="M34 64 L68 64 L60 56 L42 56 Z" fill="none" stroke="#3b2a22" stroke-width="2"/></svg>
    <h3>Unbeatable Location</h3>
    <p>Minutes from Morvane National Park, with adventure nearby and peaceful surroundings away from the crowds.</p>
  </div>
  <div class="feature" style="left:358px">
    <svg class="icon" viewBox="0 0 102 82"><circle cx="51" cy="51" r="49" fill="none" stroke="#3b2a22" stroke-width="2"/><path d="M30 66 L48 38 L56 50 L62 42 L74 66 Z" fill="#3b2a22"/><circle cx="42" cy="34" r="5" fill="#3b2a22"/></svg>
    <h3>Comfort Meets Wilderness</h3>
    <p>Our domes are insulated, climate-controlled, and thoughtfully furnished.</p>
  </div>
  <div class="feature" style="left:617px">
    <svg class="icon" viewBox="0 0 102 82"><circle cx="51" cy="51" r="49" fill="none" stroke="#3b2a22" stroke-width="2"/><path d="M38 52 L62 40 L65 46 L41 58 Z" fill="#3b2a22"/><path d="M50 54 L42 70 M52 54 L60 70" stroke="#3b2a22" stroke-width="2.5"/><circle cx="60" cy="28" r="6" fill="none" stroke="#3b2a22" stroke-width="2"/><circle cx="36" cy="30" r="1.5" fill="#3b2a22"/><circle cx="72" cy="36" r="1.5" fill="#3b2a22"/></svg>
    <h3>Incredible Stargazing</h3>
    <p>Far from city lights, our property offers breathtaking night skies.</p>
  </div>
  <div class="feature" style="left:877px">
    <svg class="icon" viewBox="0 0 102 82"><circle cx="51" cy="51" r="49" fill="none" stroke="#3b2a22" stroke-width="2"/><circle cx="51" cy="36" r="5" fill="#3b2a22"/><path d="M44 44 H58 L60 58 H42 Z" fill="#3b2a22"/><path d="M34 64 Q51 54 68 64" stroke="#3b2a22" stroke-width="3" fill="none"/><path d="M51 20v5M39 24l3 4M63 24l-3 4" stroke="#3b2a22" stroke-width="2"/></svg>
    <h3>Designed for Relaxation</h3>
    <p>The sounds of nature create an atmosphere where you can truly unplug and recharge.</p>
  </div>
</section>

<section>
  <svg class="domes-bg" width="1200" height="720" viewBox="0 0 1200 720">
    <path d="M0 0 H1200 V503 Q600 930 0 503 Z" fill="#3b2a22"/>
  </svg>
  <h2 class="abs heading domes-title">Our Domes</h2>
  <span class="rule" style="left:112px;top:1987px;background:#fff"></span>
  <p class="abs domes-text" style="top:2018px">Experience the perfect blend of nature and comfort in our thoughtfully designed geodesic domes. Surrounded by forest and fresh mountain air, each dome offers a cozy retreat after a day of exploring Morvane National Park.</p>
  <p class="abs domes-text" style="top:2147px;height:104px;overflow:hidden">Enjoy comfortable beds, climate-controlled interiors, and modern touches that make your stay relaxing in every season. Whether you’re visiting for adventure or quiet escape, our domes provide a unique glamping experience you won’t forget.</p>
  <a class="btn btn-light" style="left:112px;top:2279px;width:142px;height:49px">Read More</a>
  <svg class="abs" style="left:590px;top:1920px" width="552" height="420" viewBox="0 0 552 420">
    <path d="M16 412 A266 266 0 1 1 536 412" fill="none" stroke="#fff" stroke-width="8"/>
  </svg>
  <div class="domes-photo" role="img" aria-label="Night photo of a lit geodesic dome among pine trees under the northern lights"></div>
</section>

<section>
  <h2 class="abs heading gallery-title">Our Gallery</h2>
  <span class="rule" style="left:570px;top:2715px"></span>
  <div class="tile" style="left:112px;top:2774px;width:309px;height:380px;background:linear-gradient(180deg,#c9ccd0 0%,#e9ecef 50%,#9a8874 100%)" role="img" aria-label="White geodesic dome on a wooden deck among bare birch trees"></div>
  <div class="tile tile-banner" style="left:430px;top:2769px;width:661px;height:197px"><span class="dot"></span><span class="name">Tollen Ridge Canvas Camps</span></div>
  <div class="tile" style="left:432px;top:2975px;width:406px;height:179px;background:linear-gradient(90deg,#2e3a2c 0%,#4a5646 50%,#dfe2e3 100%)" role="img" aria-label="Clear dome beside evergreen forest with a red chair"></div>
  <div class="tile" style="left:848px;top:2975px;width:239px;height:179px;background:linear-gradient(180deg,#9fb3d6 0%,#c7d4ea 60%,#e8eef7 100%)" role="img" aria-label="Snow-covered dome in a winter landscape"></div>
  <a class="btn btn-dark" style="left:536px;top:3222px;width:142px;height:50px">View More</a>
</section>

<footer>
  <svg class="footer-shape" width="1200" height="571" viewBox="0 0 1200 571">
    <path d="M0 219 Q600 -170 1200 219 V571 H0 Z" fill="#000"/>
    <path d="M112 150 Q600 -100 1088 150 Q600 -40 112 150 Z" fill="#3b2a22"/>
  </svg>
  <div class="abs footer-brand"><span class="dot"></span><span class="name">Tollen Ridge<br>Canvas Camps</span></div>

  <div class="footer-col">
    <h4 style="left:498px">Quick Links</h4>
    <ul style="left:498px">
      <li><svg width="14" height="14" viewBox="0 0 14 14"><path d="M1 7h10M7 2l5 5-5 5" stroke="#fff" stroke-width="2" fill="none"/></svg>Home</li>
      <li><svg width="14" height="14" viewBox="0 0 14 14"><path d="M1 7h10M7 2l5 5-5 5" stroke="#fff" stroke-width="2" fill="none"/></svg>About</li>
      <li><svg width="14" height="14" viewBox="0 0 14 14"><path d="M1 7h10M7 2l5 5-5 5" stroke="#fff" stroke-width="2" fill="none"/></svg>Gallery</li>
      <li><svg width="14" height="14" viewBox="0 0 14 14"><path d="M1 7h10M7 2l5 5-5 5" stroke="#fff" stroke-width="2" fill="none"/></svg>Experiences</li>
      <li><svg width="14" height="14" viewBox="0 0 14 14"><path d="M1 7h10M7 2l5 5-5 5" stroke="#fff" stroke-width="2" fill="none"/></svg>Contact Us</li>
    </ul>
  </div>
  <div class="footer-col">
    <h4 style="left:690px">Help Links</h4>
    <ul style="left:690px">
      <li><svg width="14" height="14" viewBox="0 0 14 14"><path d="M1 7h10M7 2l5 5-5 5" stroke="#fff" stroke-width="2" fill="none"/></svg>FAQ</li>
      <li><svg width="14" height="14" viewBox="0 0 14 14"><path d="M1 7h10M7 2l5 5-5 5" stroke="#fff" stroke-width="2" fill="none"/></svg>Terms of use</li>
      <li><svg width="14" height="14" viewBox="0 0 14 14"><path d="M1 7h10M7 2l5 5-5 5" stroke="#fff" stroke-width="2" fill="none"/></svg>Privacy Policy</li>
      <li><svg width="14" height="14" viewBox="0 0 14 14"><path d="M1 7h10M7 2l5 5-5 5" stroke="#fff" stroke-width="2" fill="none"/></svg>Support Links</li>
      <li><svg width="14" height="14" viewBox="0 0 14 14"><path d="M1 7h10M7 2l5 5-5 5" stroke="#fff" stroke-width="2" fill="none"/></svg>Conditions</li>
    </ul>
  </div>
  <div class="footer-col"><h4 style="left:872px">Contact Us</h4></div>
  <div class="contact-item" style="top:3596px"><span class="ic"><svg width="16" height="18" viewBox="0 0 16 18"><path d="M8 1a6 6 0 0 1 6 6c0 5-6 10-6 10S2 12 2 7a6 6 0 0 1 6-6z" fill="#000"/><circle cx="8" cy="7" r="2.2" fill="#fff"/></svg></span><span>morvane national park in<br>Alberta, Canada.</span></div>
  <div class="contact-item" style="top:3662px"><span class="ic"><svg width="16" height="16" viewBox="0 0 16 16"><path d="M3 1l3 3-2 2c1 2 3 4 5 5l2-2 3 3-2 3C6 15 1 10 0 3z" fill="#000"/></svg></span><span style="line-height:32px">+1 555 014 2290</span></div>
  <div class="contact-item" style="top:3713px"><span class="ic"><svg width="16" height="12" viewBox="0 0 16 12"><rect x="0" y="0" width="16" height="12" rx="1.5" fill="#000"/><path d="M1 1l7 6 7-6" stroke="#fff" stroke-width="1.5" fill="none"/></svg></span><span style="line-height:32px">info@tollenridge.com</span></div>
  <div class="footer-rule"></div>
  <p class="copyright">Copyrights2026.Tollen Ridge Canvas Camps.All Rights Reserved</p>
</footer>

</body>
</html>
```